Business Card Design

Company is a Commercial Building Company specialising in New Construction and existing refurbishments

Industry/Entity Type

Business

Contact Information for Business Card

Liam Porter
Construction Manager
E Liam@marshbuilding.com.au
M 0400 213 594
Mail 14 Tarrant Rise Kestrel Bay WA 6214

```html
<!DOCTYPE html>
<html lang="en">
<head>
<meta charset="utf-8">
<title>Marsh Building &amp; Construction – Business Card</title>
<link rel="stylesheet" href="https://fonts.googleapis.com/css2?family=Roboto:wght@300;400;500&display=swap">
<style>
  :root {
    --canvas-bg: #e9e7e4;
    --card-white: #ffffff;
    --card-black: #050505;
    --brand-cyan: #1fb3d1;
    --brand-orange: #f08a1c;
    --ink-dark: #2b2e34;
    --ink-light: #ffffff;
  }
  * { margin: 0; padding: 0; box-sizing: border-box; }
  html, body { width: 1200px; height: 848px; overflow: hidden; }
  body {
    background: var(--canvas-bg);
    font-family: "Roboto", Arial, sans-serif;
    display: flex;
    flex-direction: column;
    align-items: center;
    justify-content: center;
    gap: 56px;
  }
  .card {
    position: relative;
    width: 560px;
    height: 320px;
    background: var(--card-white);
    overflow: hidden;
    box-shadow: 0 6px 18px rgba(0,0,0,0.18);
  }

  .wordmark {
    display: flex;
    align-items: center;
    gap: 12px;
  }
  .wordmark__square {
    width: 22px;
    height: 22px;
    background: var(--brand-cyan);
  }
  .wordmark__name {
    color: var(--ink-dark);
    font-weight: 500;
    font-size: 17px;
    line-height: 1.1;
    letter-spacing: 0.5px;
    text-transform: uppercase;
  }

  .person__name {
    color: var(--brand-cyan);
    font-weight: 300;
    font-size: 30px;
    line-height: 1;
  }
  .person__title {
    color: var(--brand-orange);
    font-weight: 300;
    font-size: 19px;
    margin-top: 4px;
  }

  .card--front .front__logo-area {
    height: 46%;
    display: flex;
    align-items: center;
    justify-content: center;
  }
  .card--front .front__band {
    position: absolute;
    left: 0; right: 0; bottom: 0;
    height: 54%;
    background: var(--card-black);
    padding: 26px 30px;
    display: flex;
    justify-content: space-between;
    align-items: flex-start;
  }
  .card--front .person { margin-top: 30px; }
  .contact {
    list-style: none;
    text-align: right;
    color: var(--ink-light);
    font-weight: 300;
    font-size: 13px;
    line-height: 1.75;
  }
  .contact__item {
    display: flex;
    justify-content: flex-end;
    align-items: center;
    gap: 8px;
  }
  .contact__icon { width: 11px; height: 11px; flex: none; }

  .card--back .back__stripes {
    position: absolute;
    top: 0; left: 0; right: 0;
  }
  .back__stripe { height: 5px; }
  .back__stripe--cyan { background: var(--brand-cyan); }
  .back__stripe--orange { background: var(--brand-orange); }
  .card--back .back__logo-area {
    position: absolute;
    top: 10px; left: 0; right: 0;
    height: 200px;
    display: flex;
    align-items: center;
    justify-content: center;
  }
  .card--back .back__band {
    position: absolute;
    left: 0; right: 0; bottom: 0;
    height: 110px;
    background: var(--card-black);
    padding: 24px 34px;
    display: flex;
    justify-content: flex-end;
  }
  .card--back .person { text-align: left; }
</style>
</head>
<body>

  <section class="card card--front" aria-label="Business card front">
    <div class="front__logo-area">
      <div class="wordmark">
        <span class="wordmark__square"></span>
        <span class="wordmark__name">Marsh Building<br>&amp; Construction</span>
      </div>
    </div>
    <div class="front__band">
      <div class="person">
        <p class="person__name">Liam Porter</p>
        <p class="person__title">Construction Manager</p>
      </div>
      <ul class="contact">
        <li class="contact__item">0400 213 594
          <svg class="contact__icon" viewBox="0 0 12 12"><rect x="3" y="0.5" width="6" height="11" rx="1" fill="none" stroke="#f08a1c" stroke-width="1.2"/><circle cx="6" cy="9.5" r="0.8" fill="#f08a1c"/></svg>
        </li>
        <li class="contact__item">Liam@marshbuilding.com.au
          <svg class="contact__icon" viewBox="0 0 12 12"><rect x="0.5" y="2" width="11" height="8" fill="#f08a1c"/><path d="M0.5 2 L6 6.5 L11.5 2" fill="none" stroke="#050505" stroke-width="1"/></svg>
        </li>
        <li class="contact__item">Mail 14 Tarrant Rise Kestrel Bay WA 6214
          <svg class="contact__icon" viewBox="0 0 12 12"><path d="M6 11.5 C3 7.5 2 6 2 4.2 A4 4 0 0 1 10 4.2 C10 6 9 7.5 6 11.5Z" fill="#f08a1c"/><circle cx="6" cy="4.3" r="1.5" fill="#050505"/></svg>
        </li>
      </ul>
    </div>
  </section>

  <section class="card card--back" aria-label="Business card back">
    <div class="back__stripes">
      <div class="back__stripe back__stripe--cyan"></div>
      <div class="back__stripe back__stripe--orange"></div>
    </div>
    <div class="back__logo-area">
      <div class="wordmark">
        <span class="wordmark__square"></span>
        <span class="wordmark__name">Marsh Building<br>&amp; Construction</span>
      </div>
    </div>
    <div class="back__band">
      <div class="person">
        <p class="person__name">Liam Porter</p>
        <p class="person__title">Construction Manager</p>
      </div>
    </div>
  </section>

</body>
</html>
```